Home Security Company Business Card

Looking for a eye catching business card that is non traditional and stands out but yet still looks professional. It should include all the pertinent information such as name, title, address, telephone, e-mail, website address should definitely stand out and then finally the logo.

Target Market(s)

Residential and Commercial accounts mostly upscale accounts

Industry/Entity Type

Security

Contact Information for Business Card

Name
Title
Address
Office #
Cell #
E-mail
Website

Font styles to use
Serif
Sans Serif

Requirements
Must have
• Logo, two sided color configuration
Nice to have
• You decide
Should not have
• There really aren't any.

```html
<!DOCTYPE html>
<html lang="en">
<head>
<meta charset="utf-8">
<title>Ironvale Security Systems Inc. – Business Card</title>
<link rel="stylesheet" href="https://fonts.googleapis.com/css2?family=Cinzel:wght@600&family=Marcellus&display=swap">
<style>
  :root {
    --crimson: #9e1b1f;
    --crimson-dark: #7f1317;
    --gold: #d7a93a;
    --gold-light: #f3e6b8;
    --gold-mid: #d9c270;
    --gold-deep: #b9982f;
    --paper: #f7f7f5;
    --backdrop: #e9e6e0;
    --ink-white: #ffffff;
  }
  * { box-sizing: border-box; margin: 0; padding: 0; }
  html, body { width: 1200px; height: 780px; overflow: hidden; }
  body {
    background: var(--backdrop);
    position: relative;
    font-family: "Marcellus", serif;
  }

  .card {
    position: absolute;
    box-shadow: 0 10px 28px rgba(0,0,0,.18);
    overflow: hidden;
  }

  /* Front */
  .card-front {
    left: 90px; top: 60px;
    width: 380px; height: 660px;
    background: var(--paper);
    display: flex; flex-direction: column; align-items: center;
  }
  .brand {
    margin-top: 90px;
    display: flex; flex-direction: column; align-items: center;
    color: var(--crimson);
    font-family: "Cinzel", serif; font-weight: 600;
  }
  .brand-dot {
    width: 54px; height: 54px; border-radius: 50%;
    background: var(--crimson);
    margin-bottom: 18px;
  }
  .brand-name { font-size: 40px; letter-spacing: 1px; line-height: 1; }
  .brand-tag { font-size: 14.5px; letter-spacing: 1.2px; margin-top: 4px; }

  .person { margin-top: 52px; text-align: center; }
  .person-name { color: var(--crimson); font-size: 30px; letter-spacing: 1px; }
  .person-title { color: var(--gold); font-size: 18px; letter-spacing: 1px; margin-top: -2px; }

  .contact {
    margin-top: 34px;
    list-style: none;
    color: var(--crimson);
    font-size: 19px; letter-spacing: .5px; line-height: 1.45;
    text-align: left;
  }
  .contact li { display: flex; align-items: center; gap: 10px; }
  .contact-icon {
    width: 20px; height: 20px;
    background: var(--gold);
    display: inline-flex; align-items: center; justify-content: center;
    border-radius: 2px;
  }
  .contact-plain { padding-left: 0; }

  .web-band {
    position: absolute; left: 0; right: 0; bottom: 0;
    height: 92px;
    background: linear-gradient(var(--crimson), var(--crimson-dark));
    color: var(--ink-white);
    font-size: 22px; letter-spacing: 2px;
    display: flex; align-items: center; justify-content: center;
  }

  /* Back */
  .card-back {
    left: 520px; top: 207px;
    width: 640px; height: 366px;
    background: radial-gradient(ellipse at 55% 50%, var(--gold-light) 0%, var(--gold-mid) 55%, var(--gold-deep) 100%);
    display: flex; flex-direction: column; align-items: center; justify-content: center;
    color: var(--crimson);
    font-family: "Cinzel", serif; font-weight: 600;
  }
  .back-name { font-size: 74px; letter-spacing: 2px; line-height: 1; }
  .back-tag { font-size: 27px; letter-spacing: 2px; margin-top: 8px; }
</style>
</head>
<body>
  <section class="card card-front" aria-label="Business card front">
    <div class="brand">
      <span class="brand-dot"></span>
      <span class="brand-name">IRONVALE</span>
      <span class="brand-tag">SECURITY SYSTEMS INC.</span>
    </div>

    <div class="person">
      <p class="person-name">Marcus Hale</p>
      <p class="person-title">Owner</p>
    </div>

    <ul class="contact">
      <li>
        <span class="contact-icon">
          <svg width="14" height="14" viewBox="0 0 24 24" aria-hidden="true"><path fill="#fff" d="M6.6 10.8a15 15 0 0 0 6.6 6.6l2.2-2.2a1 1 0 0 1 1-.25 11.4 11.4 0 0 0 3.6.6 1 1 0 0 1 1 1V20a1 1 0 0 1-1 1A17 17 0 0 1 3 4a1 1 0 0 1 1-1h3.5a1 1 0 0 1 1 1c0 1.25.2 2.45.6 3.6a1 1 0 0 1-.25 1z"/></svg>
        </span>
        555-014-2290
      </li>
      <li>
        <span class="contact-icon">
          <svg width="12" height="14" viewBox="0 0 20 24" aria-hidden="true"><rect x="4" y="1" width="12" height="22" rx="2" fill="#fff"/><rect x="6" y="4" width="8" height="13" fill="#d7a93a"/></svg>
        </span>
        +1 555-014-2290
      </li>
      <li class="contact-plain">info@ironvalesec.com</li>
      <li class="contact-plain">PO Box 418 Harbor Lane, USA</li>
    </ul>

    <div class="web-band">www.ironvalesec.com</div>
  </section>

  <section class="card card-back" aria-label="Business card back">
    <span class="back-name">IRONVALE</span>
    <span class="back-tag">SECURITY SYSTEMS INC.</span>
  </section>
</body>
</html>
```